Business Card Design for Training Business

Clear Path Coaching is a new business that delivers training and other services with a focus on topics related to mental health and wellbeing, for example, Wellmind Response Course, Resilience etc. We have a strong focus on evidence-based psychology and neuroscience. I have a logo which I will upload with the brief, so please consider colours that work well with the logo.
Target Market(s)
Adults, workplaces (particularly government and not-for-profits)
Industry/Entity Type
Business
Contact Information for Business Card
Head Strong TrainingSamantha SellwoodDirector0438 770 850sam@headstrongtraining.com.auwww.headstrongtraining.com.au

```html
<!DOCTYPE html>
<html lang="en">
<head>
<meta charset="utf-8">
<title>Clear Path Coaching – Business Card</title>
<link rel="stylesheet" href="https://fonts.googleapis.com/css2?family=Open+Sans:wght@300;400;700&display=swap">
<style>
  :root {
    --page-bg: #e9e6e2;
    --card-white: #f7f7f7;
    --brown: #6f6360;
    --stone: #a69a96;
    --teal: #3fc0c6;
    --teal-soft: #9adde0;
    --ink-light: #b9b9b9;
    --text-white: #ffffff;
    --text-soft: #ece8e6;
  }
  * { box-sizing: border-box; margin: 0; padding: 0; }
  html, body {
    width: 1200px; height: 1022px; overflow: hidden;
    background: var(--page-bg);
    font-family: "Open Sans", Arial, sans-serif;
  }
  .card {
    position: absolute;
    left: 100px; top: 225px;
    width: 1000px; height: 571px;
    border-radius: 22px;
    overflow: hidden;
    background: var(--card-white);
    box-shadow: 0 18px 40px rgba(60, 45, 35, 0.25);
  }
  .card__shapes { position: absolute; inset: 0; width: 100%; height: 100%; }

  .brand {
    position: absolute;
    left: 60px; top: 232px;
    display: flex; align-items: center; gap: 24px;
  }
  .brand__dot {
    width: 96px; height: 96px; border-radius: 50%;
    border: 3px solid var(--teal);
  }
  .brand__name {
    font-weight: 300;
    color: var(--ink-light);
    text-transform: uppercase;
    line-height: 1.1;
    text-align: center;
  }
  .brand__name span { display: block; }
  .brand__line1 { font-size: 38px; letter-spacing: 3px; }
  .brand__line2 { font-size: 16px; letter-spacing: 12px; margin-top: 6px; padding-left: 12px; }

  .contact {
    position: absolute;
    right: 78px; top: 118px;
    text-align: right;
    color: var(--text-soft);
  }
  .contact__name {
    font-size: 36px; font-weight: 700; color: var(--text-white);
    letter-spacing: 0.3px;
  }
  .contact__role { font-size: 21px; color: var(--teal); margin-top: 2px; }
  .contact__phone { font-size: 21px; font-weight: 300; margin-top: 44px; }
  .contact__web {
    position: absolute; right: 0; top: 300px;
    white-space: nowrap;
    font-size: 20px; font-weight: 300; line-height: 1.45;
  }

  .icons {
    position: absolute;
    right: 30px; top: 135px;
    display: flex; flex-direction: column; gap: 12px;
  }
  .icons svg { width: 22px; height: 22px; display: block; }
</style>
</head>
<body>
  <section class="card" aria-label="Business card front">
    <svg class="card__shapes" viewBox="0 0 1000 571" preserveAspectRatio="none" aria-hidden="true">
      <path class="panel" d="M430 0 L1000 0 L1000 571 L380 571 C470 470 560 360 565 240 C570 130 520 40 430 0 Z" fill="var(--brown)"/>
      <path class="stripe stripe--stone" d="M565 240 C560 360 470 470 380 571 L350 571 C445 475 548 370 565 240 Z" fill="var(--stone)"/>
      <path class="stripe stripe--teal" d="M560 262 C543 385 440 480 344 571 L320 571 C420 480 533 390 560 262 Z" fill="var(--teal)"/>
      <path class="stripe stripe--teal-soft" d="M553 300 C528 410 428 490 312 571 L302 571 C418 490 518 410 553 300 Z" fill="var(--teal-soft)"/>
    </svg>

    <div class="brand">
      <div class="brand__dot"></div>
      <div class="brand__name">
        <span class="brand__line1">Clear Path</span>
        <span class="brand__line2">Coaching</span>
      </div>
    </div>

    <div class="icons">
      <svg viewBox="0 0 24 24" aria-label="Phone"><path d="M6.6 3.5 9 6.8 7.4 9.2c1.2 2.6 3 4.4 5.4 5.6l2.4-1.6 3.3 2.4-1 3.4C10.6 19.3 4.5 13.2 3.2 4.5Z" fill="var(--teal)"/></svg>
      <svg viewBox="0 0 24 24" aria-label="Email"><rect x="3" y="5" width="18" height="14" rx="2" fill="none" stroke="var(--teal)" stroke-width="2"/><path d="M3.5 6 12 13l8.5-7" fill="none" stroke="var(--teal)" stroke-width="2"/></svg>
      <svg viewBox="0 0 24 24" aria-label="Website"><circle cx="12" cy="12" r="9" fill="none" stroke="var(--teal)" stroke-width="2"/><path d="M3 12h18M12 3c3 3 3 15 0 18M12 3c-3 3-3 15 0 18" fill="none" stroke="var(--teal)" stroke-width="1.6"/></svg>
    </div>

    <div class="contact">
      <p class="contact__name">Rebecca Tanfield</p>
      <p class="contact__role">Director</p>
      <p class="contact__phone">0491 362 517</p>
      <div class="contact__web">
        <p>bec@clearpathcoaching.example.au</p>
        <p>www.clearpathcoaching.example.au</p>
      </div>
    </div>
  </section>
</body>
</html>
```